Powepoint template for an investment group

Need high end clear clean concise creative luxurious

Have royal clients
High end/billionaire investors

Using ross gold logo can be creative
Must habe page numbers
Logo preference header top right
Page number footer bottom right

The first page of the ppt maybe a big block of dark grey and veltro investment group written on the front page in rose gold

Target Market(s)

Investors at a high level

Requirements
Must have
• Luxury feel

```html
<!DOCTYPE html>
<html lang="en">
<head>
<meta charset="utf-8">
<title>Veltro Investment Group – Presentation Template</title>
<link href="https://fonts.googleapis.com/css2?family=Roboto:wght@300;400;500;700&display=swap" rel="stylesheet">
<style>
  :root{
    --rose:#c08476;
    --rose-deep:#b7796b;
    --rose-pale:#f3c6bd;
    --ink:#1f1f1f;
    --ink-bar:#2e2e2e;
    --bar-rose:#bb8679;
    --text:#4a4a4a;
    --white:#ffffff;
    --stage-light:#cfcfcf;
    --stage-dark:#9a9a9a;
  }
  *{margin:0;padding:0;box-sizing:border-box;}
  html,body{width:1200px;height:1099px;overflow:hidden;}
  body{
    font-family:"Roboto",Arial,sans-serif;
    background:radial-gradient(ellipse at 50% 50%,var(--stage-light) 0%,var(--stage-dark) 75%);
    position:relative;
  }
  .slide{position:absolute;width:525px;height:295px;overflow:hidden;box-shadow:0 10px 28px rgba(0,0,0,.45);}
  .col-left{left:67px;} .col-right{left:608px;}
  .row-1{top:85px;} .row-2{top:402px;} .row-3{top:719px;}
  .dark{background:var(--ink);}
  .light{background:var(--white);}

  .slide-header{position:absolute;left:0;top:0;width:100%;height:33px;background:var(--ink);z-index:3;}
  .slide-title{position:absolute;left:26px;top:5px;font-size:22px;font-weight:400;color:var(--rose);letter-spacing:.2px;}
  .header-brand{position:absolute;right:11px;top:6px;color:var(--rose);font-weight:300;text-align:center;line-height:1;}
  .header-brand .name{display:block;font-size:14px;letter-spacing:4px;margin-right:-4px;}
  .header-brand .sub{display:block;font-size:4.6px;letter-spacing:.6px;margin-top:2px;}
  .slide-body{position:absolute;left:0;top:33px;width:100%;height:262px;}

  .page-number{position:absolute;right:9px;bottom:10px;width:21px;height:19px;background:var(--rose-deep);color:var(--white);
    font-size:8.5px;font-weight:700;display:flex;align-items:center;justify-content:center;z-index:5;}

  /* cover */
  .cover-brand{position:absolute;left:0;right:0;top:86px;text-align:center;color:var(--rose);font-weight:300;}
  .cover-brand .name{display:block;font-size:64px;letter-spacing:14px;margin-right:-14px;line-height:1;}
  .cover-brand .sub{display:block;font-size:25px;letter-spacing:3px;margin-top:22px;}

  /* team */
  .team-backdrop{position:absolute;left:0;bottom:0;width:100%;height:120px;
    background:linear-gradient(180deg,rgba(255,255,255,0) 0%,rgba(160,160,160,.45) 60%,rgba(110,110,110,.75) 100%);}
  .team-card{position:absolute;top:0;width:150px;text-align:center;}
  .team-card .person-name{position:absolute;top:157px;left:0;width:100%;font-size:10.5px;font-weight:500;color:var(--ink);}
  .team-card .bio{position:absolute;top:179px;left:0;width:100%;font-size:7.4px;line-height:13.4px;color:var(--text);}

  /* about */
  .about-copy{position:absolute;left:22px;top:22px;width:285px;font-size:7.6px;line-height:13.4px;color:var(--text);text-align:justify;}
  .about-copy p+p{margin-top:26px;}

  /* finance */
  .finance-copy{position:absolute;left:253px;top:26px;width:245px;font-size:7.6px;line-height:13.4px;color:var(--text);text-align:justify;}
  .finance-copy p+p{margin-top:13.4px;}
  .axis-label{position:absolute;font-size:8px;color:var(--ink);}

  /* why */
  .why-backdrop{position:absolute;inset:0;background:linear-gradient(135deg,#fafafa 0%,#eeeeee 45%,#e6e4e4 70%,#f5f5f5 100%);}
  .feature{position:absolute;width:250px;height:90px;}
  .feature svg{position:absolute;left:0;top:0;}
  .feature h3{position:absolute;left:79px;top:6px;font-size:10.5px;font-weight:500;color:var(--ink);white-space:nowrap;}
  .feature p{position:absolute;left:79px;top:28px;width:145px;font-size:7.4px;line-height:13.4px;color:var(--text);}

  /* closing */
  .closing-box{position:absolute;left:260px;top:64px;width:265px;height:166px;background:var(--ink);text-align:center;color:var(--rose);font-weight:300;}
  .closing-box .name{display:block;font-size:46px;letter-spacing:10px;margin-right:-10px;line-height:1;margin-top:22px;}
  .closing-box .sub{display:block;font-size:17px;letter-spacing:2px;margin-top:14px;}
  .closing-box .thanks{display:block;font-size:23px;font-weight:700;color:var(--white);margin-top:17px;letter-spacing:.5px;}
</style>
</head>
<body>

<!-- 01 Cover -->
<section class="slide dark col-left row-1">
  <div class="cover-brand"><span class="name">VELTRO</span><span class="sub">Investment Group</span></div>
  <div class="page-number">01</div>
</section>

<!-- 04 Team -->
<section class="slide light col-right row-1">
  <header class="slide-header">
    <h2 class="slide-title">OUR TEAM</h2>
    <div class="header-brand"><span class="name">VELTRO</span><span class="sub">Investment Group</span></div>
  </header>
  <div class="slide-body">
    <div class="team-backdrop" role="img" aria-label="Faded city skyline photo"></div>
    <div class="team-card" style="left:20px;">
      <svg width="150" height="155" viewBox="0 0 150 155">
        <polygon points="75,17 129,71 75,125 21,71" fill="#c9ccd1" role="img" aria-label="Portrait of John Doe"/>
        <polyline points="12,79 75,144 138,79" fill="none" stroke="#b7796b" stroke-width="8"/>
      </svg>
      <div class="person-name">JOHN DOE</div>
      <p class="bio">Lorem ipsum dolor sit amet, consectetur adipiscing eiusmod tempor incididunt ut labore et dolagna aliquaum suspendisse ultrices gravidas commodo viverra</p>
    </div>
    <div class="team-card" style="left:188px;">
      <svg width="150" height="155" viewBox="0 0 150 155">
        <polygon points="75,17 129,71 75,125 21,71" fill="#d6dadb" role="img" aria-label="Portrait of Smitha John"/>
        <polyline points="12,79 75,144 138,79" fill="none" stroke="#b7796b" stroke-width="8"/>
      </svg>
      <div class="person-name">SMITHA JOHN</div>
      <p class="bio">Lorem ipsum dolor sit amet, consectetur adipiscing eiusmod tempor incididunt ut labore et dolagna aliquaum suspendisse ultrices gravidas commodo viverra</p>
    </div>
    <div class="team-card" style="left:355px;">
      <svg width="150" height="155" viewBox="0 0 150 155">
        <polygon points="75,17 129,71 75,125 21,71" fill="#8f8c86" role="img" aria-label="Portrait of Keswhg"/>
        <polyline points="12,79 75,144 138,79" fill="none" stroke="#b7796b" stroke-width="8"/>
      </svg>
      <div class="person-name">KESWHG</div>
      <p class="bio">Lorem ipsum dolor sit amet, consectetur adipiscing eiusmod tempor incididunt ut labore et dolagna aliquaum suspendisse ultrices gravidas commodo viverra</p>
    </div>
  </div>
  <div class="page-number">04</div>
</section>

<!-- 02 About -->
<section class="slide light col-left row-2">
  <header class="slide-header">
    <h2 class="slide-title">ABOUT</h2>
    <div class="header-brand"><span class="name">VELTRO</span><span class="sub">Investment Group</span></div>
  </header>
  <div class="slide-body">
    <div class="about-copy">
      <p>Lorem ipsum dolor sit amet, consectetur adipiscing eiusmod tempor incididunt ut labore et dolore magna aliqua. Quis ipsum suspendisse ultrices gravidas commodo viverra maecenas accumsan lacus vel facilisis. Lorem ipsum dolor sit ametnsectetur adipiscing elit, sed do eiusmod tempor incididunt ut labore et dolore magna aliqua. Quis ipsum suspendisse ultrices gravida. Risus commodo viverranas accumsan lacus vel facilisis. Lorem ipsum dolor sit amet, consectetur adipiscing ed do eiusmod tempor incididunt ut labore et dolore magna aliqua. Quis ipsum suspendisse ultrices gravida. Risus commodo viverra maecenas accumsan lacus vel facilisis</p>
      <p>Lorem ipsum dolor sit amet, consectetur adipiscing eiusmod tempor incididunt ut labore et dolore magna aliqua. Quis ipsum suspendisse ultrices gravidas commodo viverra maecenas accumsan lacus vel facilisis. Lorem ipsum dolor sit ametnsectetur adipiscing elit, sed do eiusmod tempor incididunt ut labore et dolore magna aliqua. Quis ipsum suspendisse ultrices gravida. Risus commodo viverranas accumsan lacus vel facilisis. Lorem ipsum dolor sit amet,</p>
    </div>
    <svg width="525" height="262" viewBox="0 0 525 262" style="position:absolute;left:0;top:0;">
      <defs>
        <linearGradient id="towerTone" x1="0" y1="0" x2="1" y2="1">
          <stop offset="0" stop-color="#e9e9e9"/><stop offset=".5" stop-color="#9c9c9c"/><stop offset="1" stop-color="#3e3e3e"/>
        </linearGradient>
        <linearGradient id="deskTone" x1="0" y1="0" x2="1" y2="1">
          <stop offset="0" stop-color="#8a1f12"/><stop offset=".5" stop-color="#d9724f"/><stop offset="1" stop-color="#f1d5cb"/>
        </linearGradient>
      </defs>
      <polygon points="456,0 525,0 525,262 314,262" fill="url(#towerTone)" role="img" aria-label="Glass office tower seen from below"/>
      <polygon points="332,18 332,192 500,104" fill="#ffffff"/>
      <polygon points="337,26 337,185 487,104" fill="url(#deskTone)" role="img" aria-label="Hands reviewing financial charts on a desk"/>
    </svg>
  </div>
  <div class="page-number">02</div>
</section>

<!-- 05 Financial analysis -->
<section class="slide light col-right row-2">
  <header class="slide-header">
    <h2 class="slide-title">FINANCIAL ANALYSIS</h2>
    <div class="header-brand"><span class="name">VELTRO</span><span class="sub">Investment Group</span></div>
  </header>
  <div class="slide-body">
    <svg width="240" height="262" viewBox="0 0 240 262" style="position:absolute;left:0;top:0;">
      <polyline points="14,9 14,254 233,254" fill="none" stroke="#c9c9c9" stroke-width="1"/>
      <rect x="24" y="14" width="18" height="229" fill="#2e2e2e"/>
      <rect x="49" y="52" width="18" height="191" fill="#bb8679"/>
      <rect x="73" y="79" width="18" height="164" fill="#2e2e2e"/>
      <rect x="98" y="123" width="18" height="120" fill="#bb8679"/>
      <rect x="122" y="101" width="18" height="142" fill="#2e2e2e"/>
      <rect x="146" y="167" width="18" height="76" fill="#bb8679"/>
      <rect x="171" y="86" width="18" height="157" fill="#2e2e2e"/>
      <rect x="195" y="136" width="18" height="107" fill="#bb8679"/>
    </svg>
    <span class="axis-label" style="left:4px;top:4px;">Y</span>
    <span class="axis-label" style="left:239px;top:248px;">X</span>
    <div class="finance-copy">
      <p>Lorem ipsum dolor sit amet, consectetur adipiiusmod tempor incididunt ut labore et dolore magna aliqua. Quis ipsumrices gravidas commodo viverra maecenas accumsan lacus vel facilisis. Lorem ipsum dolor sit ametnsectetur adipiscing elit, sed do eiusmod tempor incididunt ut labore et dolore magna aliq suspendisse ultriodo viverranas accumsan lacus vel facilisis. Lorem ipsum dolor sit nsectetur adipisci eiusmod tempor incididunt ut labore et dolore m suspendisse ultrices gravida. Risus commodo viverra maecenas accumsan lacus vel facilisis</p>
      <p>Lorem ipsum dolor sit amet, consectetur adipid tempor incididunt ut labore et dolore magna aliquis ipsum suspendisse ultavidas commodo viverra maecenas accumsan lacus vel facilisis. Lorem ipsum dolor sit ametnsectetur adipiscing elit, sed do eiusmod tempor incididunt ut labore et dolore magna alpsum suspendisse ultrices gravs commodo viverranas accumsan lacus vel facilisis. Lorem ipsum dolor sit amet,</p>
    </div>
  </div>
  <div class="page-number">05</div>
</section>

<!-- 03 Why choose us -->
<section class="slide light col-left row-3">
  <header class="slide-header">
    <h2 class="slide-title">WHY CHOOSE US</h2>
    <div class="header-brand"><span class="name">VELTRO</span><span class="sub">Investment Group</span></div>
  </header>
  <div class="slide-body">
    <div class="why-backdrop" role="img" aria-label="Faded photo of a business handshake over documents"></div>

    <div class="feature" style="left:16px;top:32px;">
      <svg width="90" height="84" viewBox="0 0 90 84">
        <polygon points="0,41 71,0 71,82" fill="#e9c8c0"/>
        <polygon points="10,0 10,82 82,41" fill="#1f1f1f"/>
        <g fill="none" stroke="#fff" stroke-width="1.3">
          <circle cx="34" cy="41" r="16"/><line x1="34" y1="25" x2="34" y2="57"/><line x1="18" y1="41" x2="50" y2="41"/>
          <text x="22" y="53" font-size="8" fill="#fff" stroke="none" font-family="Roboto,sans-serif">%</text>
          <text x="37" y="53" font-size="8" fill="#fff" stroke="none" font-family="Roboto,sans-serif">$</text>
        </g>
      </svg>
      <h3>ADIPISCING ELIT</h3>
      <p>Lorem ipsum dolor sit amet, consectetur adipiscing eiusmod tempor incididunt ut labore et dolagna aliquaum suspendisse ultrices gravidas commodo viverra</p>
    </div>

    <div class="feature" style="left:284px;top:32px;">
      <svg width="90" height="84" viewBox="0 0 90 84">
        <polygon points="0,41 71,0 71,82" fill="#e9c8c0"/>
        <polygon points="10,0 10,82 82,41" fill="#1f1f1f"/>
        <g fill="none" stroke="#fff" stroke-width="1.3">
          <rect x="19" y="44" width="4" height="8"/><rect x="26" y="39" width="4" height="13"/><rect x="33" y="34" width="4" height="18"/><rect x="40" y="30" width="4" height="22"/>
          <polyline points="18,38 28,30 34,33 46,22"/><polyline points="41,22 46,22 46,27"/>
        </g>
      </svg>
      <h3>EXCEPTEUR SINT OCC</h3>
      <p>Lorem ipsum dolor sit amet, consectetur adipiscing eiusmod tempor incididunt ut labore et dolagna aliquaum suspendisse ultrices gravidas commodo viverra</p>
    </div>

    <div class="feature" style="left:16px;top:155px;">
      <svg width="90" height="84" viewBox="0 0 90 84">
        <polygon points="0,41 71,0 71,82" fill="#e9c8c0"/>
        <polygon points="10,0 10,82 82,41" fill="#1f1f1f"/>
        <g fill="none" stroke="#fff" stroke-width="1.3">
          <path d="M28 28 h8 l-2 4 c7 3 9 10 8 16 h-20 c-1-6 1-13 8-16 z"/>
          <text x="29" y="46" font-size="9" fill="#fff" stroke="none" font-family="Roboto,sans-serif">$</text>
          <rect x="18" y="44" width="9" height="3"/><rect x="18" y="48" width="9" height="3"/><rect x="18" y="52" width="9" height="3"/>
        </g>
      </svg>
      <h3>NEMO ENIM IPSAM</h3>
      <p>Lorem ipsum dolor sit amet, consectetur adipiscing eiusmod tempor incididunt ut labore et dolagna aliquaum suspendisse ultrices gravidas commodo viverra</p>
    </div>

    <div class="feature" style="left:284px;top:155px;">
      <svg width="90" height="84" viewBox="0 0 90 84">
        <polygon points="0,41 71,0 71,82" fill="#e9c8c0"/>
        <polygon points="10,0 10,82 82,41" fill="#1f1f1f"/>
        <g fill="none" stroke="#fff" stroke-width="1.3">
          <circle cx="36" cy="34" r="6"/>
          <text x="33.5" y="37" font-size="7" fill="#fff" stroke="none" font-family="Roboto,sans-serif">$</text>
          <rect x="16" y="38" width="5" height="10"/>
          <path d="M21 40 h8 l6 3 h8 M21 47 h10 l14 -5"/>
        </g>
      </svg>
      <h3>NEQUE PORRO QUISQ</h3>
      <p>Lorem ipsum dolor sit amet, consectetur adipiscing eiusmod tempor incididunt ut labore et dolagna aliquaum suspendisse ultrices gravidas commodo viverra</p>
    </div>
  </div>
  <div class="page-number">03</div>
</section>

<!-- 06 Closing -->
<section class="slide dark col-right row-3">
  <svg width="525" height="295" viewBox="0 0 525 295" style="position:absolute;left:0;top:0;">
    <defs>
      <linearGradient id="meetingTone" x1="0" y1="0" x2="1" y2="1">
        <stop offset="0" stop-color="#3b3a3a"/><stop offset=".45" stop-color="#b9ab98"/><stop offset="1" stop-color="#dcd8d2"/>
      </linearGradient>
    </defs>
    <polygon points="23,148 169,0 300,0 446,148 300,295 169,295" fill="url(#meetingTone)" role="img" aria-label="Top view of a team meeting around a desk with charts and a laptop"/>
    <polygon points="300,0 374,0 442,64 368,64" fill="#f3c6bd"/>
    <polygon points="368,230 442,230 374,295 300,295" fill="#f3c6bd"/>
  </svg>
  <div class="closing-box">
    <span class="name">VELTRO</span>
    <span class="sub">Investment Group</span>
    <span class="thanks">THANK YOU</span>
  </div>
  <div class="page-number">06</div>
</section>

</body>
</html>
```